Silvermoor Property Development Co.

We need a logo and business card design for a Hong Kong based real estate company, PLX Land. We are want the brand to reflect the owners forward thinking, creative, and trend setting projects, while also reflecting a sense of security and strength. We invest in industrial properties which we convert to co-living or co-working spaces. PLX stands for Greater Bay Area which is the region around southern China including HK, Macau, and 9 other Chinese cities...made up of approx. 68 million people. There are massive infrastructure projects including the bridge to Macau and high-speed rail to SZ and the bridge connecting SZ and Zhongshan.

Target Market(s)

Chinese and western retail investors, as well as institutional investors

Industry/Entity Type

Real Estate Development

Contact Information for Business Card

Dale Whitford
CEO
dale@plxland-example.com
M + 852 9581 4062
F + 852 3864 2217
Suite 2207, The Halvern, 41 Tremont Rd., Central, Hong Kong

Logo Text

plx land (company name) lifestyle property development (underneath)

Colors

Designer to choose colors to be used in the design.

Requirements
Must have
• Details listed above. One side should include the logo and company name...plx land in modern, hip styling with "lifestyle property development"
Nice to have
• Could be a Black card, with metallic purple "plx" and white "land"...but open great design ideas
Should not have
• boring and traditional layout

```html
<!DOCTYPE html>
<html lang="en">
<head>
<meta charset="utf-8">
<title>PLX Land — Business Card</title>
<link href="https://fonts.googleapis.com/css2?family=Oswald:wght@400;500&family=Open+Sans:wght@400&display=swap" rel="stylesheet">
<style>
  :root {
    --backdrop: #e8e6e4;
    --card-light: #ffffff;
    --card-light-edge: #f1f0f1;
    --charcoal: #3b3e3f;
    --purple-bright: #b01fb3;
    --text-light: #f2f2f2;
    --text-dark: #333335;
  }
  * { box-sizing: border-box; margin: 0; padding: 0; }
  html, body {
    width: 1200px;
    height: 900px;
    overflow: hidden;
    background: var(--backdrop);
  }
  .card {
    position: absolute;
    left: 111px;
    top: 147px;
    width: 978px;
    height: 605px;
    background: linear-gradient(100deg, var(--card-light) 40%, var(--card-light-edge) 100%);
    box-shadow: 0 10px 30px rgba(0,0,0,0.12);
    overflow: hidden;
  }
  .card__panel {
    position: absolute;
    inset: 0;
    width: 100%;
    height: 100%;
  }
  .contact {
    position: absolute;
    left: 58px;
    top: 232px;
    color: var(--text-light);
    font-family: "Open Sans", Arial, sans-serif;
  }
  .contact__name {
    font-family: "Oswald", "Arial Narrow", sans-serif;
    font-weight: 400;
    font-size: 34px;
    line-height: 1.1;
    color: var(--purple-bright);
    text-transform: uppercase;
  }
  .contact__role {
    font-size: 25px;
    line-height: 1.3;
    margin-bottom: 14px;
  }
  .contact__lines { list-style: none; }
  .contact__line {
    display: flex;
    align-items: center;
    gap: 8px;
    font-size: 25px;
    line-height: 35px;
  }
  .contact__icon { width: 20px; height: 20px; flex: none; }
  .contact__address {
    font-style: normal;
    font-size: 25px;
    line-height: 35px;
    margin-top: 16px;
  }
  .brand {
    position: absolute;
    left: 552px;
    top: 168px;
    width: 380px;
  }
  .brand__name {
    display: flex;
    align-items: center;
    gap: 14px;
    font-family: "Open Sans", Arial, sans-serif;
    font-weight: 400;
    font-size: 54px;
    line-height: 1;
    color: var(--text-dark);
    white-space: nowrap;
  }
  .brand__mark {
    width: 22px;
    height: 22px;
    background: var(--purple-bright);
    flex: none;
  }
  .brand__tagline {
    margin-top: 40px;
    font-family: "Oswald", "Arial Narrow", sans-serif;
    font-weight: 500;
    font-size: 24px;
    color: var(--text-dark);
    white-space: nowrap;
  }
</style>
</head>
<body>
  <div class="card">
    <svg class="card__panel" viewBox="0 0 652 403" preserveAspectRatio="none" aria-hidden="true">
      <polygon points="0,0 213,0 430,403 0,403" fill="var(--charcoal)"/>
      <polygon points="213,0 221,0 440,403 430,403" fill="var(--purple-bright)"/>
    </svg>

    <section class="contact">
      <h1 class="contact__name">Dale Whitford</h1>
      <p class="contact__role">CEO</p>
      <ul class="contact__lines">
        <li class="contact__line">
          <svg class="contact__icon" viewBox="0 0 20 20" aria-hidden="true"><rect x="5" y="1" width="10" height="18" rx="2" fill="none" stroke="var(--purple-bright)" stroke-width="2"/><rect x="8.5" y="15" width="3" height="2" fill="var(--purple-bright)"/></svg>
          + 852 9581 4062
        </li>
        <li class="contact__line">
          <svg class="contact__icon" viewBox="0 0 20 20" aria-hidden="true"><rect x="5" y="2" width="10" height="5" fill="var(--purple-bright)"/><rect x="2" y="7" width="16" height="7" rx="1.5" fill="var(--purple-bright)"/><rect x="5" y="12" width="10" height="6" fill="var(--purple-bright)" stroke="var(--charcoal)" stroke-width="1"/></svg>
          + 852 3864 2217
        </li>
        <li class="contact__line">
          <svg class="contact__icon" viewBox="0 0 20 20" aria-hidden="true"><rect x="2" y="5" width="16" height="11" fill="var(--purple-bright)"/><polyline points="2,5 10,11 18,5" fill="none" stroke="var(--charcoal)" stroke-width="1.5"/></svg>
          dale@plxland-example.com
        </li>
      </ul>
      <address class="contact__address">
        Suite 2207, The Halvern<br>
        41 Tremont Rd.,<br>
        Central, Hong Kong
      </address>
    </section>

    <section class="brand">
      <p class="brand__name"><span class="brand__mark" aria-hidden="true"></span>PLX Land</p>
      <p class="brand__tagline">LIFESTYLE PROPERTY DEVELOPMENT</p>
    </section>
  </div>
</body>
</html>
```